Business card por a urban DJ, up scale audience target

Need a sober design, modern, conservative colors but i can consider some options, y play rnb, hip hop, EDM and top40.

Business card for contact and personal info, double sided, use logo attrached please; im 42 so i need a card acording to my age an target audience.

Target Market(s)

Adult people, up scale audience

Industry/Entity Type

Music Download

Contact Information for Business Card

Cel (318) 4207265518 www.lumadrift.com

Requirements
Must have
• open mind
Nice to have
• open mind
Should not have
• DJ

```html
<!DOCTYPE html>
<html lang="en">
<head>
<meta charset="utf-8">
<title>LUMA – Business Card</title>
<link rel="stylesheet" href="https://fonts.googleapis.com/css2?family=Arimo:wght@400;700&display=swap">
<style>
  :root {
    --page: #e9e7e4;
    --card-white: #f4f4f4;
    --ink: #111111;
    --band-grey: #7a7a7a;
    --logo-dark: #333333;
    --text-light: #ffffff;
    --text-soft: #d6d6d6;
    --icon-bg: #e6e6e6;
  }
  * { margin: 0; padding: 0; box-sizing: border-box; }
  html, body {
    width: 1200px; height: 902px; overflow: hidden;
    background: var(--page);
    font-family: "Arimo", Arial, sans-serif;
  }
  .canvas {
    width: 1200px; height: 902px;
    display: flex; flex-direction: column;
    align-items: center; justify-content: center; gap: 34px;
  }
  .card {
    position: relative;
    width: 700px; height: 400px;
    box-shadow: 0 8px 24px rgba(0,0,0,0.18);
    overflow: hidden;
  }

  /* Back side */
  .card--back {
    background: var(--ink);
    display: flex; align-items: center; justify-content: center;
  }
  .back-brand { display: flex; align-items: center; gap: 16px; }
  .back-brand__mark { width: 26px; height: 26px; background: var(--text-light); }
  .back-brand__name {
    font-weight: 700; font-size: 96px; letter-spacing: 4px;
    color: var(--text-light); line-height: 1;
  }

  /* Front side */
  .card--front {
    background: linear-gradient(160deg, #ffffff 0%, var(--card-white) 60%, #e4e4e4 100%);
  }
  .card__swoosh { position: absolute; inset: 0; width: 100%; height: 100%; }
  .brand {
    position: absolute; left: 48px; top: 150px;
    display: flex; align-items: center; gap: 12px;
  }
  .brand__mark { width: 22px; height: 22px; background: var(--logo-dark); }
  .brand__name {
    font-weight: 700; font-size: 72px; letter-spacing: 3px;
    color: var(--logo-dark); line-height: 1;
  }
  .contact { position: absolute; right: 36px; left: 0; top: 0; bottom: 0; color: var(--text-soft); }
  .contact > * { position: absolute; right: 0; text-align: right; white-space: nowrap; }
  .contact__name { top: 136px; font-size: 24px; font-weight: 700; color: var(--text-light); }
  .contact__title { top: 166px; font-size: 17px; right: 0; }
  .contact__line {
    display: flex; align-items: center; gap: 10px;
    font-size: 16px; height: 24px;
  }
  .contact__line--phone { top: 210px; }
  .contact__line--web { top: 242px; }
  .contact__line--mail { top: 274px; }
  .contact__line--address { top: 306px; }
  .icon {
    width: 20px; height: 20px; background: var(--icon-bg);
    display: flex; align-items: center; justify-content: center; flex: none;
  }
  .icon svg { width: 14px; height: 14px; }
</style>
</head>
<body>
<div class="canvas">
  <div class="card card--back">
    <div class="back-brand">
      <span class="back-brand__mark"></span>
      <span class="back-brand__name">LUMA</span>
    </div>
  </div>

  <div class="card card--front">
    <svg class="card__swoosh" viewBox="0 0 700 400" preserveAspectRatio="none" aria-hidden="true">
      <path d="M0,400 C200,392 300,290 370,190 C430,100 540,52 700,42 L700,400 Z" fill="var(--band-grey)"/>
      <path d="M20,400 C220,395 330,300 400,200 C460,115 560,80 700,75 L700,400 Z" fill="var(--ink)"/>
    </svg>

    <div class="brand">
      <span class="brand__mark"></span>
      <span class="brand__name">LUMA</span>
    </div>

    <div class="contact">
      <div class="contact__name">Marcus Whitfield</div>
      <div class="contact__title">Managing Director</div>
      <div class="contact__line contact__line--phone">(318) 4207265518
        <span class="icon"><svg viewBox="0 0 24 24"><path d="M6 3h4l2 5-3 2a12 12 0 0 0 5 5l2-3 5 2v4a2 2 0 0 1-2 2A17 17 0 0 1 4 5a2 2 0 0 1 2-2z" fill="#222"/></svg></span>
      </div>
      <div class="contact__line contact__line--web">www.lumadrift.com
        <span class="icon"><svg viewBox="0 0 24 24" fill="none" stroke="#222" stroke-width="2"><circle cx="12" cy="12" r="9"/><path d="M3 12h18M12 3c3 3 3 15 0 18M12 3c-3 3-3 15 0 18"/></svg></span>
      </div>
      <div class="contact__line contact__line--mail">info@lumadrift.com
        <span class="icon"><svg viewBox="0 0 24 24" fill="none" stroke="#222" stroke-width="2"><rect x="3" y="6" width="18" height="12"/><path d="M3 6l9 7 9-7"/></svg></span>
      </div>
      <div class="contact__line contact__line--address">47 Harbor Lane, Suite Easton MA 0412
        <span class="icon"><svg viewBox="0 0 24 24"><path d="M12 2a7 7 0 0 0-7 7c0 5 7 13 7 13s7-8 7-13a7 7 0 0 0-7-7zm0 10a3 3 0 1 1 0-6 3 3 0 0 1 0 6z" fill="#222"/></svg></span>
      </div>
    </div>
  </div>
</div>
</body>
</html>
```